Payment company requires web design

We need a web design for a new company based in Singapore.

The company focuses on providing 2 key products: 1) an alternative payment option (i.e. like quib or trelloquin options) on the traditional checkout process 2) a replacement/outsource of a merchants payment page. Key in the UX flow is a end customer dashboard that manages all payments.

We look to provide a simple, fluid and easy to use payment process. The dashboard is minimalistic that allows easy navigation, review of transactions and all available options through gamification.

The final design should communicate ease of use, flexibility and transparency.

Target Market(s)

The value is for the merchant - retail/travel/insurance companies. However its the merchant's end customers that are the target and who the UX is built for.

Industry/Entity Type

It Company

Logo Text

zelnar

Number of Pages Required

5+ page

Colors
ec1f27

Requirements
Must have
• 7 pages mimicking UX flow
• payment page * 2 - 1) alternative payment type 2) outsource of merchants payment page to our business
• our landing page
• end customer verification page
• end customer registration
• customer dashboard
• UX flow in attached file
Nice to have
• open to ideas
• have asked for the logo to be added
• logo to have the colour red (chinese for prosperity)
• the company is all about flexibility, transparency in personal finance management with the option of instalment payments

```html
<!DOCTYPE html>
<html lang="en">
<head>
<meta charset="utf-8">
<title>Zelnar — Payment Processing</title>
<link rel="stylesheet" href="https://fonts.googleapis.com/css2?family=Catamaran:wght@400;500;600&family=Open+Sans:wght@400;600&display=swap">
<style>
:root{
  --red:#ec1f27;
  --ink:#222222;
  --text:#555555;
  --muted:#777777;
  --soft:#f5f5f5;
  --line:#e4e4e4;
  --white:#ffffff;
}
*{margin:0;padding:0;box-sizing:border-box}
html,body{width:1200px;height:2956px;overflow:hidden}
body{font-family:"Open Sans",Arial,sans-serif;color:var(--text);background:var(--white);position:relative}
.heading{font-family:"Catamaran",Helvetica,sans-serif;font-weight:400;color:var(--red);letter-spacing:.5px}
.btn{display:flex;align-items:center;justify-content:center;background:var(--red);color:var(--white);font-family:"Catamaran",Helvetica,sans-serif;font-weight:600;font-size:12px;letter-spacing:.6px;text-transform:uppercase;border-radius:3px;position:absolute}
.copy{font-size:11px;line-height:24px;color:var(--text)}
section,header,footer{position:absolute;left:0;width:1200px}

/* hero */
.hero{top:0;height:568px;overflow:hidden}
.hero-photo{position:absolute;inset:0;background:linear-gradient(100deg,#f3f3f3 0%,#e8e8e8 35%,#d9d9db 60%,#cfcfd2 80%,#ececec 100%)}
.hero-photo::after{content:"";position:absolute;left:330px;top:350px;width:320px;height:170px;border-radius:12px;background:linear-gradient(135deg,#f2593d,#d8261d);opacity:.55;transform:rotate(18deg)}
.nav{position:absolute;top:38px;left:130px;right:130px;height:36px;display:flex;align-items:center}
.brand{display:flex;align-items:center;gap:10px;font-family:"Catamaran",Helvetica,sans-serif;font-weight:600;font-size:28px;color:var(--red);letter-spacing:1px}
.brand-mark{width:22px;height:22px;background:var(--red);border-radius:3px}
.nav-links{margin-left:auto;display:flex;gap:46px;font-family:"Catamaran",Helvetica,sans-serif;font-size:12px;font-weight:500;letter-spacing:1px;color:#333}
.nav-links span.more::after{content:"";display:inline-block;margin-left:6px;border:4px solid transparent;border-top-color:#333;vertical-align:-2px}
.nav-actions{display:flex;gap:8px;margin-left:42px}
.nav-login{width:80px;height:32px;border:1px solid #555;border-radius:3px;font-family:"Catamaran",sans-serif;font-size:12px;font-weight:600;display:flex;align-items:center;justify-content:center;color:#333;letter-spacing:.5px}
.nav-start{position:static;width:104px;height:32px}
.hero-title{position:absolute;top:192px;width:100%;text-align:center;font-size:48px}
.hero-sub{position:absolute;top:280px;width:100%;text-align:center;font-size:13px;color:#444}
.hero-cta{left:489px;top:341px;width:222px;height:53px;font-size:14px}

/* welcome */
.welcome{top:568px;height:338px;text-align:center}
.welcome .heading{position:absolute;top:54px;width:100%;font-size:34px}
.welcome .copy{position:absolute;top:118px;left:230px;width:740px;text-align:center}
.welcome .btn{left:552px;top:224px;width:96px;height:34px}

/* personal finance */
.finance{top:906px;height:467px;background:var(--soft)}
.finance-photo{position:absolute;left:0;top:0;width:720px;height:467px;background:linear-gradient(90deg,#e6e6e6 0%,#efefef 60%,#f5f5f5 100%)}
.finance .heading{position:absolute;left:504px;top:110px;font-size:34px}
.finance .copy{position:absolute;left:504px;top:182px;width:566px}
.finance .btn{left:504px;top:315px;width:97px;height:36px}

/* installments */
.installments{top:1373px;height:398px}
.installments-photo{position:absolute;left:713px;top:0;width:487px;height:398px;background:linear-gradient(180deg,#f7f3ef 0%,#eadfd6 55%,#d9b9a2 100%)}
.installments .heading{position:absolute;left:130px;top:82px;font-size:34px}
.installments .copy{position:absolute;left:130px;top:150px;width:566px}
.installments .btn{left:130px;top:290px;width:98px;height:34px}

/* faq */
.faq{top:1771px;height:489px;background:var(--soft)}
.faq .heading{position:absolute;top:54px;width:100%;text-align:center;font-size:34px}
.faq-list{position:absolute;left:134px;top:158px;width:940px;list-style:none}
.faq-item{position:relative;padding-left:37px;font-family:"Catamaran",sans-serif;font-size:14px;color:var(--ink);margin-bottom:16px}
.faq-item::before{content:"";position:absolute;left:4px;top:7px;border:5px solid transparent}
.faq-item.open::before{border-top-color:var(--ink);top:9px}
.faq-item.closed::before{border-bottom-color:var(--ink);top:3px}
.faq-answer{font-family:"Open Sans",sans-serif;font-size:11px;line-height:22px;color:var(--muted);margin-top:4px;margin-bottom:26px}
.faq .btn{left:536px;top:386px;width:128px;height:36px}

/* testimonial */
.testimonial{top:2260px;height:404px}
.testimonial .heading{position:absolute;top:74px;width:100%;text-align:center;font-size:34px}
.arrow{position:absolute;top:2454px;width:36px;height:80px}
.avatar{position:absolute;left:236px;top:2439px;width:134px;height:134px;border-radius:50%;background:linear-gradient(160deg,#8a8f96,#c2a08a 60%,#6d6a68)}
.quote{position:absolute;left:410px;top:2429px;width:551px;height:140px;background:var(--soft);text-align:center;padding-top:24px;font-size:13px;line-height:24px;color:var(--muted)}
.quote cite{display:block;font-style:normal;font-weight:600;color:var(--red);font-size:13px;margin-top:2px}

/* footer */
.footer{top:2664px;height:212px;background:var(--soft)}
.footer h4{font-family:"Catamaran",sans-serif;font-weight:500;font-size:20px;color:var(--ink);position:absolute;top:36px}
.footer ul{list-style:none;position:absolute;top:80px;font-size:11px;line-height:23px;color:#444}
.mail-input{position:absolute;left:130px;top:80px;width:244px;height:44px;background:var(--white);border:1px solid var(--line);font-size:11px;color:#999;padding:14px 12px}
.footer .btn{left:132px;top:141px;width:93px;height:36px;font-size:11px;text-transform:none}
.bottom-bar{top:2876px;height:80px;border-top:1px solid var(--line);background:var(--soft)}
.bottom-bar .legal{position:absolute;left:130px;top:26px;font-size:11px;color:#333}
.social{position:absolute;right:110px;top:24px;display:flex;gap:14px;font-family:"Catamaran",sans-serif;font-weight:600;font-size:14px;color:#333}
</style>
</head>
<body>

<header class="hero">
  <div class="hero-photo" role="img" aria-label="Photo of a hand holding a red payment card beside an open laptop keyboard"></div>
  <nav class="nav">
    <div class="brand"><span class="brand-mark"></span>ZELNAR</div>
    <div class="nav-links"><span>PRICING</span><span>BLOG</span><span class="more">MORE</span></div>
    <div class="nav-actions">
      <span class="nav-login">LOGIN</span>
      <span class="btn nav-start">Get Started</span>
    </div>
  </nav>
  <h1 class="heading hero-title">Payment Processing</h1>
  <p class="hero-sub">Lorem ipsum dolor sit amet, consectetur adipiscing elit, sed do eiusmod tempor incididunt</p>
  <span class="btn hero-cta">Start Free Trial</span>
</header>

<section class="welcome">
  <h2 class="heading">Welcome to Zelnar</h2>
  <p class="copy">Nemo enim ipsam voluptatem quia voluptas sit aspernatur aut odit aut fugit, sed quia consequuntur magni dolores eos qui ratione voluptatem sequi nesciunt. Neque porro quisquam est, qui dolorem ipsum quia dolor sit amet, consectetur, adipisci velit, sed quia non numquam eius modi tempora incidunt ut labore et dolore magnam aliquam quaerat voluptatem.</p>
  <span class="btn">Read More</span>
</section>

<section class="finance">
  <div class="finance-photo" role="img" aria-label="Photo of a hand holding a smartphone showing the app, next to a keyboard, notepad and coffee cup"></div>
  <h2 class="heading">Personal Finance</h2>
  <p class="copy">Nemo enim ipsam voluptatem quia voluptas sit aspernatur aut odit aut fugit, sed quia consequuntur magni dolores eos qui ratione voluptatem sequi nesciunt. Neque porro quisquam est, qui dolorem ipsum quia dolor sit amet, consectetur, adipisci velit, sed quia non numquam eius modi tempora incidunt ut labore et dolore magnam aliquam quaerat voluptatem.</p>
  <span class="btn">Read More</span>
</section>

<section class="installments">
  <h2 class="heading">Installment Payments</h2>
  <p class="copy">Nemo enim ipsam voluptatem quia voluptas sit aspernatur aut odit aut fugit, sed quia consequuntur magni dolores eos qui ratione voluptatem sequi nesciunt. Neque porro quisquam est, qui dolorem ipsum quia dolor sit amet, consectetur, adipisci velit, sed quia non numquam eius modi tempora incidunt ut labore et dolore magnam aliquam quaerat voluptatem.</p>
  <span class="btn">Read More</span>
  <div class="installments-photo" role="img" aria-label="Photo of many raised hands each holding up a payment card"></div>
</section>

<section class="faq">
  <h2 class="heading">Faq</h2>
  <ul class="faq-list">
    <li class="faq-item open">About flexibility, transparency in personal finance management
      <p class="faq-answer">Nemo enim ipsam voluptatem quia voluptas sit aspernatur aut odit aut fugit, sed quia consequuntur magni dolores eos qui ratione voluptatem sequi nesciunt. Neque porro quisquam est, qui dolorem ipsum quia dolor sit amet, consectetur, adipisci velit, sed quia non numquam</p>
    </li>
    <li class="faq-item closed">Lorem ipsum dolor sit amet, consectetur adipiscing elit, sed do eiusmod tempor incididunt ut labore et dolore magna aliqua?</li>
    <li class="faq-item closed">Duis aute irure dolor in reprehenderit in voluptate velit esse cillum dolore eu fugiat nulla pariatur?</li>
  </ul>
  <span class="btn">View More</span>
</section>

<section class="testimonial">
  <h2 class="heading">Customer Testimonial</h2>
</section>
<svg class="arrow" style="left:128px" viewBox="0 0 36 80" aria-hidden="true"><polyline points="34,2 2,40 34,78" fill="none" stroke="#777" stroke-width="1.2"/></svg>
<svg class="arrow" style="left:1030px" viewBox="0 0 36 80" aria-hidden="true"><polyline points="2,2 34,40 2,78" fill="none" stroke="#777" stroke-width="1.2"/></svg>
<div class="avatar" role="img" aria-label="Round portrait photo of the customer"></div>
<blockquote class="quote">
  Nemo enim ipsam voluptatem quia voluptas sit aspernatur aut odit aut fugit,<br>
  sed quia consequuntur magni dolores eos qui ratione voluptatem<br>
  sequi nesciunt. Neque porro quisquam est,
  <cite>-John Doe -</cite>
</blockquote>

<footer class="footer">
  <h4 style="left:130px">Newsletter</h4>
  <div class="mail-input">Enter Your Mail id</div>
  <span class="btn">Subscribe</span>

  <h4 style="left:433px">Company</h4>
  <ul style="left:433px"><li>About Zelnar</li><li>Our Team</li><li>Careers</li><li>Contact us</li></ul>

  <h4 style="left:622px">Get Started</h4>
  <ul style="left:622px"><li>Group</li><li>International</li><li>China</li><li>Zelnar Branch</li><li>Zelnar Marketplace</li></ul>

  <h4 style="left:817px">Learn</h4>
  <ul style="left:817px"><li>Case Studies</li><li>Guides</li><li>Blog</li><li>FAQ</li></ul>

  <h4 style="left:969px">Legal Info</h4>
  <ul style="left:969px"><li>Risk Warnings</li><li>Privacy Policy</li><li>Terms of Service</li><li>Referral Fee</li></ul>
</footer>

<div class="bottom-bar" style="position:absolute;left:0;width:1200px">
  <p class="legal">© 2016 Zelnar. All Right Reserved.</p>
  <div class="social"><span>chirpa</span><span>folia</span><span>linkwell</span><span>circlo</span></div>
</div>

</body>
</html>
```